Personal Blog

The wordpress blog style and layout should be similar to http://www.samfenwick.com

homepage: my photo, list of things, call to action then 3 boxes (The Blog, The Book and podcast)

Other pages: About us, Blog, Consulting, Contact

Target Market(s)

Web Marketing Consultant

Industry/Entity Type

Consulting

Colors
3277b5
33a6d7
f04a50
f68e4e
33b7a4

```html
<!DOCTYPE html>
<html lang="en">
<head>
<meta charset="utf-8">
<title>Nadim Farouk — Web Marketing Consultant</title>
<link href="https://fonts.googleapis.com/css2?family=Dosis:wght@400;500;600;700&family=Arimo:wght@400;700&display=swap" rel="stylesheet">
<style>
:root{
  --ink:#2f3338;
  --header:#3a3f45;
  --footer:#3b4046;
  --footer-dark:#2c3035;
  --page:#e9eaec;
  --white:#ffffff;
  --text:#3c3c3c;
  --muted:#8a8d91;
  --orange:#f68e4e;
  --red:#f04a50;
  --blue:#3277b5;
  --sky:#33a6d7;
  --teal:#33b7a4;
  --line:#e2e2e2;
}
*{box-sizing:border-box;margin:0;padding:0}
html,body{width:1200px;height:3375px;overflow:hidden}
body{background:var(--page);font-family:"Arimo",Arial,sans-serif;color:var(--text);position:relative}
.heading{font-family:"Dosis",sans-serif}

/* header */
.site-header{position:absolute;left:0;top:0;width:1200px;height:150px;background:var(--header)}
.brand{position:absolute;left:30px;top:40px;display:flex;align-items:center;font-family:"Dosis",sans-serif;font-weight:700;font-size:44px;color:var(--white)}
.brand-mark{width:22px;height:22px;background:var(--orange);margin-right:14px}
.main-nav{position:absolute;right:30px;top:55px;display:flex;gap:30px;font-family:"Dosis",sans-serif;font-weight:600;font-size:22px;color:var(--white);text-transform:uppercase}
.main-nav .current{color:var(--orange)}

/* main column */
.content{position:absolute;left:45px;top:180px;width:715px;height:2690px;background:var(--white);padding:30px 32px}
.post-title{font-family:"Dosis",sans-serif;font-weight:500;font-size:40px;line-height:46px;color:var(--ink)}
.byline{margin-top:18px;font-size:16px;color:var(--muted);font-weight:700}
.byline span{color:var(--orange)}
.post-body{margin-top:20px;font-size:16px;line-height:22px;color:var(--text)}
.post-body p{margin-bottom:18px}
.post-photo{float:right;width:312px;height:462px;margin:0 0 14px 24px;background:linear-gradient(160deg,#2b2d31 0%,#4d5058 55%,#1f2024 100%)}
.accent{color:var(--orange)}
.btn{display:inline-block;background:var(--orange);color:var(--white);font-size:17px;padding:12px 26px;border-radius:3px}
.divider{border-top:1px solid var(--line);margin:34px -32px 30px}

.post-grid{display:grid;grid-template-columns:1fr 1fr;column-gap:40px;row-gap:40px}
.teaser h3{font-family:"Dosis",sans-serif;font-weight:700;font-size:26px;line-height:30px;color:var(--ink);text-transform:uppercase}
.teaser p{margin-top:14px;font-size:16px;line-height:22px}
.teaser .meta{margin-top:14px;color:var(--orange);font-size:16px}

.pagination{position:absolute;left:32px;right:32px;top:2600px;display:flex;align-items:center;gap:10px;font-size:15px}
.page{width:34px;height:34px;border:1px solid var(--line);display:flex;align-items:center;justify-content:center;color:var(--muted)}
.page-prev{background:#c9cbce;color:var(--white);padding:9px 24px;border-radius:3px;margin-right:auto}
.page-next{background:var(--orange);color:var(--white);padding:9px 30px;border-radius:3px;margin-left:auto}

/* sidebar */
.sidebar{position:absolute;left:795px;top:180px;width:360px}
.optin{background:var(--ink);color:var(--white);padding:34px 30px 30px;height:965px}
.intro{display:flex;gap:18px}
.avatar{width:105px;height:105px;border-radius:50%;background:linear-gradient(150deg,#d9c2b0,#7c6a60);border:5px solid var(--white);flex:none}
.intro p{font-size:16px;line-height:22px}
.optin .lead{margin-top:16px;font-size:16px;line-height:22px}
.optin .hot{color:var(--red)}
.optin h4{font-family:"Dosis",sans-serif;font-size:27px;line-height:31px;font-weight:700;margin-top:50px;text-transform:uppercase}
.optin .pitch{margin-top:16px;font-size:16px;line-height:22px}
.field{background:var(--white);color:#666;font-size:14px;height:40px;padding:11px 12px;margin-top:14px}
.btn-wide{display:block;text-align:center;background:var(--orange);color:var(--white);font-family:"Dosis",sans-serif;font-weight:700;font-size:26px;padding:8px;margin-top:16px}
.banner{width:360px;margin-top:20px;border:3px solid var(--white)}
.search{margin-top:30px}
.search .field{border:1px solid var(--line);margin-top:0}
.search .btn-wide{margin-top:14px}

/* footer */
.site-footer{position:absolute;left:0;top:2905px;width:1200px;height:395px;background:var(--footer);color:var(--white)}
.foot-col{position:absolute;top:40px}
.foot-col h5{font-family:"Dosis",sans-serif;font-weight:700;font-size:26px;text-transform:uppercase}
.foot-col p{font-size:15px;line-height:22px;margin-top:12px;color:#c9ccd0}
.btn-outline{display:inline-block;margin-top:14px;border:2px solid var(--red);color:var(--white);font-size:14px;padding:6px 14px}
.socials{display:grid;grid-template-columns:repeat(3,52px);gap:14px;margin-top:22px}
.social{width:52px;height:52px;border-radius:6px;background:var(--orange)}
.copyright{position:absolute;left:0;top:3300px;width:1200px;height:75px;background:var(--footer-dark);color:#c9ccd0;font-size:15px;display:flex;align-items:center;justify-content:center}
.copyright span{color:var(--orange);margin:0 5px}
</style>
</head>
<body>

<header class="site-header">
  <div class="brand"><span class="brand-mark"></span>Nadim Farouk</div>
  <nav class="main-nav">
    <span class="current">About</span><span>Blog</span><span>Consulting</span><span>Resources</span><span>Book</span><span>Contact</span>
  </nav>
</header>

<main class="content">
  <article class="featured-post">
    <h1 class="post-title">The Content Marketing Travel Kit – Everything You Need to Create &amp; Market Great Content on the Go!</h1>
    <div class="byline">by Nadim. Farouk - <span>19 comments</span></div>
    <div class="post-body">
      <div class="post-photo" role="img" aria-label="Speaker on stage holding a microphone in front of a large screen"></div>
      <p>"Lorem ipsum dolor sit amet, consectetur adipiscing elit, sed do eiusmod tempor incididunt ut labore et dolore magna aliqua. Ut enim ad minim veniam, quis nostrud exercitation ullamco laboris nisi ut aliquip ex ea commodo consequat.</p>
      <p>Duis aute irure dolor in reprehenderit in voluptate velit esse cillum dolore eu fugiat nulla pariatur. <span class="accent">Excepteur</span> sint occaecat cupidatat non proident, sunt in culpa qui officia deserunt mollit anim id est laborum.</p>
      <p>Sed ut perspiciatis unde omnis iste natus error sit voluptatem accusantium doloremque laudantium, totam rem aperiam, eaque ipsa quae ab illo inventore veritatis et quasi architecto beatae.</p>
      <p>"Lorem ipsum dolor sit amet, consectetur adipiscing elit, sed do eiusmod tempor incididunt ut labore et dolore magna aliqua</p>
      <p>"Lorem ipsum dolor sit amet, consectetur adipiscing elit, sed do eiusmod tempor incididunt ut labore et dolore magna aliqua</p>
      <p class="accent">You can click for the playlist on our video channel</p>
      <p>Duis aute irure dolor in reprehenderit in voluptate velit esse cillum dolore eu fugiat nulla pariatur. Excepteur sint occaecat cupidatat non proident, sunt in culpa qui officia deserunt mollit anim id est laborum.</p>
      <span class="btn">Read more</span>
    </div>
  </article>

  <div class="divider"></div>

  <section class="post-grid">
    <article class="teaser"><h3>7 Online Tools to Help You Create Amazing Visual Content</h3><p>When it comes to online content creation and marketing, we're becoming more and more attracted to visuals. Visual content has grown in leaps and bounds [...]</p><div class="meta">13 Comments - Read More!</div></article>
    <article class="teaser"><h3>7 Online Tools to Help You Create Amazing Visual Content</h3><p>When it comes to online content creation and marketing, we're becoming more and more attracted to visuals. Visual content has grown in leaps and bounds [...]</p><div class="meta">13 Comments - Read More!</div></article>
    <article class="teaser"><h3>7 Online Tools to Help You Create Amazing Visual Content</h3><p>When it comes to online content creation and marketing, we're becoming more and more attracted to visuals. Visual content has grown in leaps and bounds [...]</p><div class="meta">13 Comments - Read More!</div></article>
    <article class="teaser"><h3>7 Online Tools to Help You Create Amazing Visual Content</h3><p>When it comes to online content creation and marketing, we're becoming more and more attracted to visuals. Visual content has grown in leaps and bounds [...]</p><div class="meta">13 Comments - Read More!</div></article>
    <article class="teaser"><h3>7 Online Tools to Help You Create Amazing Visual Content</h3><p>When it comes to online content creation and marketing, we're becoming more and more attracted to visuals. Visual content has grown in leaps and bounds [...]</p><div class="meta">13 Comments - Read More!</div></article>
    <article class="teaser"><h3>7 Online Tools to Help You Create Amazing Visual Content</h3><p>When it comes to online content creation and marketing, we're becoming more and more attracted to visuals. Visual content has grown in leaps and bounds [...]</p><div class="meta">13 Comments - Read More!</div></article>
    <article class="teaser"><h3>7 Online Tools to Help You Create Amazing Visual Content</h3><p>When it comes to online content creation and marketing, we're becoming more and more attracted to visuals. Visual content has grown in leaps and bounds [...]</p><div class="meta">13 Comments - Read More!</div></article>
    <article class="teaser"><h3>7 Online Tools to Help You Create Amazing Visual Content</h3><p>When it comes to online content creation and marketing, we're becoming more and more attracted to visuals. Visual content has grown in leaps and bounds [...]</p><div class="meta">13 Comments - Read More!</div></article>
  </section>

  <nav class="pagination">
    <span class="page-prev">Previous</span>
    <span class="page">1</span><span class="page">2</span><span class="page">3</span><span class="page">4</span><span class="page">5</span><span class="page">…</span><span class="page">30</span>
    <span class="page-next">Next</span>
  </nav>
</main>

<aside class="sidebar">
  <section class="optin">
    <div class="intro">
      <div class="avatar" role="img" aria-label="Portrait photo of the author"></div>
      <p>"Lorem ipsum dolor sit amet, consectetur adipiscing</p>
    </div>
    <p class="lead">"Lorem ipsum dolor sit amet, consectetur adipiscing elit, sed do eiusmod tempor incididunt ut labore et dolore magna aliqua. <span class="hot">"Lorem ipsum dolor sit amet, consectetur adipiscing elit, sed do eiusmod tempor incididunt ut labore et dolore magna aliqua</span> enim ad minim veniam, quis nostrud exercitation ullamco laboris nisi ut aliquip ex ea commodo consequat.</p>
    <h4>Join my new business bootcamp for free</h4>
    <p class="pitch">Learn how to create raving fans with free eBooks, get started with online video and podcasting, engage with social media and blog your way to business success, plus much more!</p>
    <div class="field">Enter your name...</div>
    <div class="field">Enter your email...</div>
    <span class="btn-wide">JOIN FOR FREE</span>
  </section>

  <div class="banner" role="img" aria-label="Event banner with speaker headshots on a teal and orange background" style="height:340px;background:linear-gradient(180deg,#3aa8c9,#f2a25a 60%,#e8e2d0)"></div>
  <div class="banner" role="img" aria-label="Community banner with laptop illustration on a green and white background" style="height:340px;background:linear-gradient(180deg,#f4f6f2,#8fc4a2 55%,#3f8c6a)"></div>
  <div class="banner" role="img" aria-label="Staffing service banner with illustrated assistant on a sky blue background" style="height:310px;background:linear-gradient(120deg,#cdeaf6,#5fb4de 60%,#f04a50)"></div>
  <div class="banner" role="img" aria-label="Personal branding course banner with book cover on a light background" style="height:345px;background:linear-gradient(180deg,#f5f3ee,#d9cfbf 65%,#2f3338)"></div>

  <div class="search">
    <div class="field">Search Archive</div>
    <span class="btn-wide">SEARCH</span>
  </div>
</aside>

<footer class="site-footer">
  <div class="foot-col" style="left:45px;width:330px">
    <h5>Entrepreneur, Speaker,</h5>
    <p>Lorem Ipsum is simply dummy text of the printing &amp; typesetting industry. Lorem Ipsum has been the industry's standard dummy text ever since the 1500s.</p>
    <span class="btn-outline">Get the long-winded version!</span>
  </div>
  <div class="foot-col" style="left:420px;width:330px">
    <h5>Join my new business</h5>
    <div class="field">Enter your name...</div>
    <div class="field">Enter your email...</div>
    <span class="btn-wide">JOIN FOR FREE</span>
  </div>
  <div class="foot-col" style="left:800px;width:355px">
    <h5>Connect with me</h5>
    <div class="socials">
      <span class="social"></span><span class="social"></span><span class="social"></span>
      <span class="social"></span><span class="social"></span><span class="social"></span>
    </div>
    <p>OR<br>Connect with via <span style="color:var(--orange)">email</span></p>
  </div>
</footer>
<div class="copyright">© 2014 N. Farouk -<span>www.nadimfarouk.com</span>- All Right Reserved.</div>

</body>
</html>
```